Business card design for a dynamic IT consulting company

We need a business card design for a young firm, specialized in the Telecommunications/Consulting industry. The name of the company is Quindor and Partners Business Consulting Ltd. (Short name: Quindor and Partnes)
Quindor = solve read reverse, so we aim to be uncomplicated and solution-oriented. The small pipe in our logo is also related to the word solve. So we need a new business card design, which is simple, eye catching and something non traditional (I would probably prefer a square shaped design rather than a rectangle, but open for suggestions). Attached our logo.

Target Market(s)

Usually our customers are Tier1 Telecoms providers (Q-Netra, Palorix, etc) and their executives.

Industry/Entity Type

Business

Contact Information for Business Card

Name: Bence Tolnavari
Email: b.tolnavari@quindor.hu
Web: www.quindor.hu
Mobile: +36 30 518 2769
Title: Managing Director

Optional:
Company name: Quindor and Partners Ltd.
Address: 1087 Budapest, Tolvenka str. 28/C, Hungary

Font styles to use
Other font styles liked:
• helveticaneue_medium, Prime Regular are used now.

Colors

Designer to choose colors to be used in the design.

Requirements
Must have
• I would like to have a 2 sided design.
Nice to have
• I thought if we make the logo a bit bigger (without the company name), that could go to the back with the company name below. I though, if the pipe in the logo is somehow touchable on the business card, would be nice and unique.

```html
<!DOCTYPE html>
<html lang="en">
<head>
<meta charset="utf-8">
<title>Quindor &amp; Partners – Business Card</title>
<link rel="stylesheet" href="https://fonts.googleapis.com/css2?family=Roboto:wght@400;700&display=swap">
<style>
  :root {
    --stage: #5f5f5f;
    --card-light: #ffffff;
    --card-dark: #3a3a3c;
    --ink: #333333;
    --ink-soft: #555557;
    --magenta: #b5338a;
    --blue: #1b95d4;
    --white: #ffffff;
  }
  * { box-sizing: border-box; margin: 0; padding: 0; }
  html, body { width: 1200px; height: 772px; overflow: hidden; }
  body {
    background: var(--stage);
    font-family: "Roboto", Arial, sans-serif;
    position: relative;
  }
  .card {
    position: absolute;
    top: 166px;
    width: 440px;
    height: 440px;
    text-align: center;
    box-shadow: 14px 14px 18px rgba(0,0,0,0.35);
  }
  .card--front { left: 114px; background: var(--card-light); color: var(--ink); }
  .card--back { left: 644px; background: var(--card-dark); color: var(--white); }

  .brand { position: absolute; left: 0; right: 0; font-weight: 400; line-height: 1; letter-spacing: 0.5px; }
  .card--front .brand { top: 124px; font-size: 34px; color: var(--ink-soft); }
  .card--back .brand { top: 238px; font-size: 40px; color: var(--white); }

  .person { position: absolute; top: 215px; left: 0; right: 0; }
  .person__name { font-size: 22.5px; font-weight: 700; color: var(--ink); }
  .person__title { font-size: 15px; color: var(--blue); margin-top: 7px; }

  .contacts { position: absolute; top: 306px; left: 0; right: 0; font-size: 14.5px; }
  .contact { display: flex; justify-content: center; align-items: center; gap: 5px; height: 23px; }
  .contact svg { width: 18px; height: 18px; flex: none; }
  .contact b { font-weight: 700; }
  .company { font-size: 14.5px; margin-top: 3px; line-height: 23px; }

  .back-web { position: absolute; top: 389px; left: 0; right: 0; font-size: 15px; }
  .back-web b { font-weight: 700; }
</style>
</head>
<body>

<section class="card card--front">
  <div class="brand">Quindor &amp; Partners</div>

  <div class="person">
    <div class="person__name">Bence Tolnavari</div>
    <div class="person__title">Managing Director</div>
  </div>

  <div class="contacts">
    <div class="contact">
      <svg viewBox="0 0 18 18" aria-hidden="true">
        <circle cx="9" cy="9" r="9" fill="var(--magenta)"/>
        <path d="M4.5 7.5c0-1.5 2-2.3 4.5-2.3s4.5.8 4.5 2.3l-1.6.4-.4-1.2H6.5l-.4 1.2z" fill="#fff"/>
        <rect x="5.5" y="8.3" width="7" height="4.2" rx="0.8" fill="#fff"/>
        <circle cx="9" cy="10.4" r="1.1" fill="var(--magenta)"/>
      </svg>
      <span>+36 30 518 2769</span>
    </div>
    <div class="contact">
      <svg viewBox="0 0 18 18" aria-hidden="true">
        <circle cx="9" cy="9" r="9" fill="var(--magenta)"/>
        <rect x="4.3" y="5.8" width="9.4" height="6.6" fill="#fff"/>
        <path d="M4.3 5.8 9 9.8l4.7-4" fill="none" stroke="var(--magenta)" stroke-width="1"/>
      </svg>
      <span>b.tolnavari@quindor.hu</span>
    </div>
    <div class="contact">
      <svg viewBox="0 0 18 18" aria-hidden="true">
        <circle cx="9" cy="9" r="9" fill="var(--magenta)"/>
        <g fill="none" stroke="#fff" stroke-width="1">
          <circle cx="9" cy="9" r="5"/>
          <ellipse cx="9" cy="9" rx="2.2" ry="5"/>
          <path d="M4 9h10M5 6.5h8M5 11.5h8"/>
        </g>
      </svg>
      <span>www.<b>quindor</b>.hu</span>
    </div>
    <div class="company">
      Quindor and Partners Ltd.<br>
      1087 Budapest, Tolvenka str. 28/C, Hungary
    </div>
  </div>
</section>

<section class="card card--back">
  <div class="brand">Quindor &amp; Partners</div>
  <div class="back-web">www.<b>quindor</b>.hu</div>
</section>

</body>
</html>
```